New Business Card Design Project

We require a business card design for Vexalund, a newly established Indian company.
Our focus is on the development, manufacturing, and export of a diverse array of pharmaceutical products on a global scale. The card should convey a professional appearance, as our primary markets are in Africa, China, and Southeast Asian nations.
We envision a two-sided business card, with the reverse side dedicated to a logo set against a solid color or an elegantly designed pattern. The corners should be rounded. We would appreciate seeing both horizontal and vertical design options. We trust the designer to utilize their expertise in creating this design.

The content for the business card is included in the attached Word file.

Target Market(s)

Our primary markets are in Africa, China, and Southeast Asian, Latin America, Maldives, Sri Lanka

Industry/Entity Type

Pharmaceutical Manufacturing and Export

Contact Information for Business Card

Colors

Designer to choose colors to be used in the design.

Requirements
Must have
• The reverse side of the business card features solely the logo along with the tagline, "Care Beyond Borders."
Should not have
• The logo should not exceed two instances, encompassing both the front and back sides of the card.

```html
<!DOCTYPE html>
<html lang="en">
<head>
<meta charset="utf-8">
<title>Vexalund Business Card</title>
<link rel="stylesheet" href="https://fonts.googleapis.com/css2?family=Poppins:wght@400;700&family=Open+Sans:wght@300;400;600;700&display=swap">
<style>
  :root {
    --stage: #222222;
    --card: #e2e5e6;
    --card-front: #e4e4e4;
    --brand-blue: #2fa8e0;
    --brand-coral: #f2634f;
    --ink: #1c1c1c;
  }
  * { box-sizing: border-box; margin: 0; padding: 0; }
  html, body { width: 1200px; height: 711px; overflow: hidden; }
  body { background: var(--stage); position: relative; font-family: "Open Sans", sans-serif; }

  .card {
    position: absolute;
    width: 520px;
    height: 300px;
    border-radius: 26px;
    overflow: hidden;
  }

  /* Reverse side */
  .card--back {
    left: 55px; top: 120px;
    background: var(--card);
    display: flex; flex-direction: column; align-items: center; justify-content: center;
  }
  .brand { display: flex; align-items: center; gap: 12px; }
  .brand__dot { width: 22px; height: 22px; border-radius: 50%; background: var(--brand-coral); }
  .brand__name {
    font-family: "Poppins", sans-serif; font-weight: 700;
    color: var(--brand-blue); font-size: 58px; line-height: 1; letter-spacing: 0.5px;
  }
  .tagline {
    margin-top: 18px;
    font-family: "Poppins", sans-serif; font-weight: 400;
    font-size: 14px; color: var(--ink); letter-spacing: 0.5px;
  }

  /* Front side */
  .card--front {
    left: 625px; top: 290px;
    background: var(--card-front);
  }
  .front-info {
    position: absolute; right: 34px; top: 30px;
    text-align: right;
  }
  .front-info .brand { justify-content: flex-end; gap: 8px; }
  .front-info .brand__dot { width: 12px; height: 12px; }
  .front-info .brand__name { font-size: 34px; }
  .accent-bar {
    position: absolute; right: 0; top: 98px;
    width: 24px; height: 34px; background: var(--brand-coral);
  }
  .person { margin-top: 14px; font-size: 24px; color: var(--brand-blue); line-height: 1.1; }
  .person__first { font-weight: 700; }
  .person__rest { font-weight: 300; }
  .role { font-size: 12px; color: var(--ink); margin-top: 2px; letter-spacing: 0.5px; }
  .address { margin-top: 14px; font-size: 11.5px; color: var(--brand-blue); line-height: 1.45; }
  .contact { margin-top: 10px; list-style: none; font-size: 12.5px; color: var(--ink); line-height: 1.7; }
  .contact li { display: flex; justify-content: flex-end; align-items: center; gap: 8px; }
  .contact svg { width: 13px; height: 13px; flex: none; }
</style>
</head>
<body>
  <section class="card card--back" aria-label="Card reverse">
    <div class="brand">
      <span class="brand__dot"></span>
      <span class="brand__name">Vexalund</span>
    </div>
    <p class="tagline">Care Beyond Borders.</p>
  </section>

  <section class="card card--front" aria-label="Card front">
    <span class="accent-bar"></span>
    <div class="front-info">
      <div class="brand">
        <span class="brand__dot"></span>
        <span class="brand__name">Vexalund</span>
      </div>
      <p class="person"><span class="person__first">Arun</span> <span class="person__rest">K. Velhal</span></p>
      <p class="role">CEO</p>
      <p class="address">14, Kiran Nagar,<br>Ramtek, 441106, India</p>
      <ul class="contact">
        <li>+91 98000 11223
          <svg viewBox="0 0 14 14" aria-hidden="true"><rect x="3" y="1" width="8" height="12" rx="1.5" fill="none" stroke="var(--brand-coral)" stroke-width="1.4"/></svg>
        </li>
        <li>www.vexalund.com
          <svg viewBox="0 0 14 14" aria-hidden="true"><circle cx="7" cy="7" r="5.5" fill="none" stroke="var(--brand-blue)" stroke-width="1.4"/><path d="M1.5 7h11M7 1.5c2.5 3 2.5 8 0 11M7 1.5c-2.5 3-2.5 8 0 11" fill="none" stroke="var(--brand-blue)" stroke-width="1"/></svg>
        </li>
        <li>akvelhal@vexalund.com
          <svg viewBox="0 0 14 14" aria-hidden="true"><rect x="1" y="3" width="12" height="8.5" rx="1" fill="var(--brand-coral)"/><path d="M1.5 3.5 7 8l5.5-4.5" fill="none" stroke="#fff" stroke-width="1.2"/></svg>
        </li>
      </ul>
    </div>
  </section>
</body>
</html>
```